Cover page and letterhead for athlete development program

We require an exciting and dynamic cover page with a second page letterhead in a word doc format for us to use as professional stationery for letter merges and portfolio documents. We are an athlete preparation company that specialises in training up and coming sports representatives in the fitness and sports science industry. We work with athletes from ages 13 - 24 mainly. If we could have images on the cover page from the sports of:
Rugby League
Rugby Union
Hockey
Cricket
AFL
Soccer
Track and Field
Netball
Basketball
Golf
Weight training

This would be a great start. Thank you

```html
<!DOCTYPE html>
<html lang="en">
<head>
<meta charset="utf-8">
<title>Rising Contender – Letterhead</title>
<link href="https://fonts.googleapis.com/css2?family=Arimo:wght@400;700&display=swap" rel="stylesheet">
<style>
  :root{
    --backdrop:#dfe1e2;
    --paper:#ffffff;
    --ink:#1c1c1c;
    --body-grey:#8a8a8a;
    --edge-dark:#2a2a2a;
    --edge-light:#9e9e9e;
  }
  *{box-sizing:border-box;margin:0;padding:0}
  html,body{width:1200px;height:784px;overflow:hidden;background:var(--backdrop)}
  body{font-family:'Arimo',Arial,sans-serif;position:relative}
  .letterhead{
    position:absolute;left:330px;top:10px;width:540px;height:764px;
    background:var(--paper);box-shadow:0 6px 18px rgba(0,0,0,.18);overflow:hidden;
  }
  .edge-band{position:absolute;width:40px;height:240px}
  .edge-band--upper{right:0;top:160px;clip-path:polygon(100% 0,100% 100%,0 50%);
    background:linear-gradient(to left,var(--edge-dark),var(--edge-light))}
  .edge-band--lower{left:0;top:410px;clip-path:polygon(0 0,0 100%,100% 50%);
    background:linear-gradient(to right,var(--edge-dark),var(--edge-light))}
  .brand{
    position:absolute;right:48px;top:52px;display:flex;align-items:center;gap:10px;
  }
  .brand__mark{width:30px;height:30px;background:var(--ink)}
  .brand__name{
    font-weight:700;font-size:22px;letter-spacing:.06em;color:var(--ink);line-height:1;
    text-transform:uppercase;
  }
  .letter-body{
    position:absolute;left:100px;right:86px;top:130px;
    font-size:10.5px;line-height:1.42;color:var(--body-grey);
  }
  .letter-body p{margin-bottom:13px}
  .footer{position:absolute;left:0;bottom:0;width:100%;height:150px}
  .footer__art{
    position:absolute;left:30px;bottom:0;width:170px;height:140px;
    background:linear-gradient(160deg,#ececec,#d6d6d6);opacity:.8;
  }
  .footer__rule{position:absolute;left:40px;bottom:96px;width:60px;height:1px;background:#9a9a9a}
  .footer__icons{position:absolute;left:115px;bottom:88px;display:flex;gap:8px}
  .footer__icons svg{width:14px;height:14px;display:block}
  .footer__address{
    position:absolute;left:40px;bottom:62px;font-size:10px;font-weight:700;color:var(--ink);
  }
  .footer__contact{
    position:absolute;left:40px;bottom:44px;font-size:9px;color:#777;
  }
</style>
</head>
<body>
<main class="letterhead">
  <div class="edge-band edge-band--upper" role="img" aria-label="Angled grey edge accent"></div>
  <div class="edge-band edge-band--lower" role="img" aria-label="Angled grey edge accent"></div>

  <header class="brand">
    <span class="brand__mark"></span>
    <span class="brand__name">Rising Contender</span>
  </header>

  <section class="letter-body">
    <p>Lorem Ipsum is simply dummy text of the printing and typesetting industry. Lorem Ipsum has been the industry's standard dummy text ever since the 1500s, when an unknown printer took a galley of type and scrambled it to make a type specimen book. It has survived not only five centuries, but also the leap into electronic typesetting, remaining essentially unchanged. It was popularised in the 1960s with the release of Markwell sheets containing Lorem Ipsum passages, and more recently with desktop publishing software like Pagecraft Studio including versions of Lorem Ipsum.</p>
    <p>It is a long established fact that a reader will be distracted by the readable content of a page when looking at its layout. The point of using Lorem Ipsum is that it has a more-or-less normal distribution of letters, as opposed to using 'Content here, content here', making it look like readable English. Many desktop publishing packages and web page editors now use Lorem Ipsum as their default model text, and a search for 'lorem ipsum' will uncover many web sites still in their infancy. Various versions have evolved over the years, sometimes by accident, sometimes on purpose (injected humour and the like).</p>
    <p>Contrary to popular belief, Lorem Ipsum is not simply random text. It has roots in a piece of classical Latin literature from 45 BC, making it over 2000 years old. Daniel Ashcombe, a Latin professor at Brookfield College in Westvale, looked up one of the more obscure Latin words, consectetur, from a Lorem Ipsum passage, and going through the cites of the word in classical literature, discovered the undoubtable source. Lorem Ipsum comes from sections 1.10.32 and 1.10.33 of an old Latin text, using its structures to generate Lorem Ipsum which looks reasonable. The generated Lorem Ipsum is therefore always free from repetition, injected humour, or non-characteristic words etc.</p>
  </section>

  <footer class="footer">
    <div class="footer__art" role="img" aria-label="Faint silhouette of an athlete in motion"></div>
    <div class="footer__rule"></div>
    <div class="footer__icons" aria-hidden="true">
      <svg viewBox="0 0 14 14"><circle cx="7" cy="7" r="7" fill="#1c1c1c"/><path d="M7 3.2a2.4 2.4 0 0 0-2.4 2.4C4.6 7.4 7 10.6 7 10.6s2.4-3.2 2.4-5A2.4 2.4 0 0 0 7 3.2z" fill="#fff"/><circle cx="7" cy="5.6" r=".9" fill="#1c1c1c"/></svg>
      <svg viewBox="0 0 14 14"><circle cx="7" cy="7" r="7" fill="#1c1c1c"/><path d="M5 3.5l1.2 1.8-.7.9a5 5 0 0 0 2.3 2.3l.9-.7 1.8 1.2-.6 1.3c-2.9-.3-5.3-2.7-5.6-5.6z" fill="#fff"/></svg>
      <svg viewBox="0 0 14 14"><circle cx="7" cy="7" r="7" fill="#1c1c1c"/><rect x="3.6" y="4.6" width="6.8" height="4.8" fill="#fff"/><path d="M3.6 4.6L7 7.3l3.4-2.7" stroke="#1c1c1c" stroke-width=".7" fill="none"/></svg>
      <svg viewBox="0 0 14 14"><circle cx="7" cy="7" r="7" fill="#1c1c1c"/><circle cx="7" cy="7" r="3.4" stroke="#fff" stroke-width=".8" fill="none"/><path d="M3.6 7h6.8M7 3.6v6.8" stroke="#fff" stroke-width=".7"/></svg>
      <svg viewBox="0 0 14 14"><circle cx="7" cy="7" r="7" fill="#1c1c1c"/><circle cx="7" cy="7" r="3" fill="#fff"/></svg>
    </div>
    <p class="footer__address">0000 Harbour Road, Ste 000, Westvale, US 00000</p>
    <p class="footer__contact">000.000.0000 | contact@risingcontender.com.au | www.risingcontender.com.au</p>
  </footer>
</main>
</body>
</html>
```